Tiny educational app company needs a big new website

We need to re-do our ageing website (www.quietpebbleapps.com). Our site is mostly visited by primary school teachers or parents of primary school kids. 90% of our apps are iPad only so an iPad optimised design would be helpful.

We would like the monkey to remain part of the design if possible. I'm not sure if the orange/ blue/ white should stay - if you have a good design and a strong opinion it should go we could be open to change.

Target Market(s)

Teachers, parents

Industry/Entity Type

Education

Number of Pages Required

3 page

Font styles to use
Sans Serif

Colors

Designer to choose colors to be used in the design.

Requirements
Must have
• Needs to show all of our apps (somehow... open to a new way of achieving this)

```html
<!DOCTYPE html>
<html lang="en">
<head>
<meta charset="utf-8">
<title>Quiet Pebble Apps</title>
<link rel="stylesheet" href="https://fonts.googleapis.com/css2?family=Montserrat:wght@400;500;600&family=Lato:ital,wght@0,400;0,700;1,400&family=Pacifico&display=swap">
<style>
:root{
  --orange:#d9560f;
  --orange-deep:#c94a0b;
  --orange-bright:#ec6a1e;
  --peach:#f2a365;
  --blue:#2f7fc1;
  --blue-dark:#1f5f9c;
  --grey-panel:#efefef;
  --ink:#333333;
  --muted:#666666;
  --line:#d6d6d6;
  --white:#ffffff;
}
*{box-sizing:border-box;margin:0;padding:0}
html,body{width:1200px;height:3209px;overflow:hidden}
body{position:relative;background:var(--white);font-family:"Lato",Arial,sans-serif;color:var(--ink)}
.abs{position:absolute}

/* hero */
.hero-bg{left:0;top:0;width:1200px;height:680px}
.brand{left:76px;top:14px;display:flex;align-items:center;gap:10px;color:var(--white);font-family:"Montserrat",sans-serif;font-weight:600;font-size:17px;line-height:1.1;width:150px}
.brand-dot{width:44px;height:44px;border-radius:50%;background:var(--orange-bright);flex:none}
.nav{right:54px;top:34px;display:flex;gap:6px;align-items:center;list-style:none;font-family:"Montserrat",sans-serif;font-size:15px;color:var(--white)}
.nav li{padding:9px 12px}
.nav li.active{border:2px solid var(--white);border-radius:22px;padding:8px 24px;margin-right:6px}
.hero-device{left:60px;top:122px;width:640px;height:450px;border-radius:28px;background:linear-gradient(160deg,#2c2c2c,#5a5a5a 60%,#d9d9d9)}
.hero-mascot{left:750px;top:478px;width:200px;height:210px;border-radius:46% 46% 20% 20%;background:linear-gradient(180deg,#8a5a3c,#c9966b)}
.hero-title{right:76px;top:138px;white-space:nowrap;text-align:right;font-family:"Pacifico",cursive;font-weight:400;font-size:52px;line-height:80px;color:var(--white)}
.hero-list{right:78px;top:234px;list-style:none;text-align:right;font-size:15px;color:var(--white);line-height:29px}
.hero-list li::after{content:"";display:inline-block;width:9px;height:9px;border-radius:50%;background:var(--white);margin-left:14px;vertical-align:1px}
.btn-outline{left:849px;top:395px;width:274px;height:52px;border:2px solid var(--white);border-radius:26px;color:var(--white);font-family:"Montserrat",sans-serif;font-size:19px;display:flex;align-items:center;justify-content:center}

/* apps */
.section-title{font-family:"Montserrat",sans-serif;font-weight:400;text-align:center;width:1200px;left:0}
.apps-title{top:702px;font-size:42px;color:var(--orange)}
.apps-intro{left:180px;top:770px;width:840px;text-align:center;font-size:13.5px;line-height:28px;color:var(--muted)}
.app{width:170px;text-align:center;font-size:16px;line-height:24px;color:var(--ink)}
.app-tile{width:137px;height:137px;border-radius:22px;margin:0 auto 36px}
.btn-solid{background:var(--orange);color:var(--white);border-radius:26px;font-family:"Montserrat",sans-serif;font-weight:500;display:flex;align-items:center;justify-content:center}
.view-all{left:503px;top:1362px;width:196px;height:52px;font-size:18px}

/* curriculum */
.curriculum-bg{left:0;top:1500px;width:1200px;height:480px}
.toy{left:139px;top:1420px;width:160px;height:195px;border-radius:48% 48% 30% 30%;background:linear-gradient(180deg,#7b4a2c,#b77c4e)}
.curr-title{left:75px;top:1630px;font-family:"Montserrat",sans-serif;font-size:42px;color:var(--white);font-weight:400}
.curr-item{color:var(--white);font-size:15px;line-height:24px;display:flex;gap:10px;width:200px}
.curr-item svg{flex:none;margin-top:4px}

/* testimonial */
.quote-bg{left:150px;top:1925px;width:900px;height:290px}
.avatar{left:282px;top:2011px;width:82px;height:82px;border-radius:50%;border:3px solid var(--blue);background:linear-gradient(180deg,#d8c2b0,#9a7a66)}
.quote{left:389px;top:2008px;width:510px;font-style:italic;font-size:14.5px;line-height:29px;color:var(--muted)}
.client{left:834px;top:2127px;display:flex;align-items:center;gap:14px;font-family:"Montserrat",sans-serif;font-size:16px;color:var(--orange);font-weight:500}
.client::before{content:"";width:22px;height:3px;background:var(--orange)}

/* feedback */
.fb-title{top:2226px;font-size:35px;color:var(--ink)}
.fb-sub{top:2276px;font-size:17px;color:var(--muted);text-align:center;width:1200px;left:0}
.field{left:389px;width:424px;border:1px solid var(--line);border-radius:6px;font-size:14px;color:var(--muted);padding:14px 18px}
.post{left:516px;top:2569px;width:166px;height:51px;font-size:18px}

/* footer */
.footer-bg{left:0;top:2760px;width:1200px;height:449px}
.kids{left:182px;top:2674px;width:888px;height:256px;border-radius:120px 120px 20px 20px;background:linear-gradient(90deg,#e8b38e,#c65a4a 30%,#4f8fd0 55%,#e7c04a 75%,#d86aa0)}
.foot-brand{left:500px;top:2962px;width:200px;display:flex;align-items:center;justify-content:center;gap:8px;font-family:"Montserrat",sans-serif;font-weight:600;font-size:15px;color:var(--white)}
.foot-brand span.dot{width:26px;height:26px;border-radius:50%;background:var(--orange-bright);border:2px solid var(--white)}
.social{left:493px;top:3052px;display:flex;gap:6px}
.social span{width:43px;height:43px;border-radius:50%}
.foot-links{left:0;top:3112px;width:1200px;display:flex;justify-content:center;list-style:none;font-size:14.5px;color:var(--white)}
.foot-links li+li::before{content:"|";margin:0 18px}
.copyright{left:0;top:3142px;width:1200px;text-align:center;font-size:14px;color:var(--white)}
</style>
</head>
<body>

<!-- hero -->
<svg class="abs hero-bg" viewBox="0 0 1200 680" aria-hidden="true">
  <rect width="1200" height="680" fill="var(--blue)"/>
  <polygon points="470,0 1200,0 1200,680 0,680 0,460" fill="var(--orange)"/>
  <polygon points="0,460 480,300 700,680 0,680" fill="var(--peach)"/>
  <polygon points="0,660 1200,600 1200,680 0,680" fill="var(--white)"/>
</svg>
<div class="abs brand"><span class="brand-dot"></span>Quiet Pebble Apps</div>
<ul class="abs nav">
  <li class="active">HOME</li><li>APPS</li><li>CURRICULUM</li><li>SUPPORT</li><li>BLOG</li><li>FEEDBACK</li>
</ul>
<div class="abs hero-device" role="img" aria-label="Tablet showing the Co-ordinates treasure map activity"></div>
<div class="abs hero-mascot" role="img" aria-label="Cartoon monkey mascot sitting at a computer"></div>
<h1 class="abs hero-title">Co-ordinates</h1>
<ul class="abs hero-list">
  <li>4 activities + teacher tool</li><li>Map maker</li><li>Map reader</li><li>Make the shape</li><li>Compass directions.</li>
</ul>
<div class="abs btn-outline">MORE INFORMATION</div>

<!-- apps -->
<h2 class="abs section-title apps-title">Our App</h2>
<p class="abs apps-intro">At Quiet Pebble Apps, we feel that it is important to make life easier for educators... teachers AND parents. Wherever you live or teach, there is an authority that stipulates (or guides) classroom learning.</p>

<div class="abs app" style="left:114px;top:868px"><div class="app-tile" style="background:linear-gradient(160deg,#3f7fb8,#e0672a)" role="img" aria-label="Co-ordinates app icon"></div>Co-ordinates</div>
<div class="abs app" style="left:315px;top:868px"><div class="app-tile" style="background:linear-gradient(160deg,#2a6a8f,#e0672a)" role="img" aria-label="Dominoes Addition app icon"></div>Dominoes<br>Addition</div>
<div class="abs app" style="left:516px;top:868px"><div class="app-tile" style="background:linear-gradient(180deg,#e0672a,#f2c230 55%,#d62a8c)" role="img" aria-label="Fraction Wall app icon"></div>Fraction<br>Wall</div>
<div class="abs app" style="left:715px;top:868px"><div class="app-tile" style="background:linear-gradient(180deg,#1e5f86,#e0672a)" role="img" aria-label="Friends of Ten app icon"></div>Friends Of<br>Ten</div>
<div class="abs app" style="left:916px;top:868px"><div class="app-tile" style="background:linear-gradient(160deg,#1f6f9c,#4aa83a)" role="img" aria-label="Beetle Maths app icon"></div>Beetle<br>Maths</div>

<div class="abs app" style="left:114px;top:1119px"><div class="app-tile" style="background:linear-gradient(180deg,#2a92d8,#5fb84a)" role="img" aria-label="Number Lines app icon"></div>Number<br>Lines</div>
<div class="abs app" style="left:315px;top:1119px"><div class="app-tile" style="background:linear-gradient(180deg,#1e5f86,#c9c2b2)" role="img" aria-label="Place Value app icon"></div>Dominoes<br>Addition</div>
<div class="abs app" style="left:516px;top:1119px"><div class="app-tile" style="background:linear-gradient(160deg,#1e5f86,#3fae5a)" role="img" aria-label="Number grid app icon"></div>Fraction<br>Wall</div>
<div class="abs app" style="left:715px;top:1119px"><div class="app-tile" style="background:linear-gradient(160deg,#1e5f86,#e7b08c)" role="img" aria-label="Missing number app icon"></div>Friends Of<br>Ten</div>
<div class="abs app" style="left:916px;top:1119px"><div class="app-tile" style="background:linear-gradient(160deg,#e0672a,#f4f4f4)" role="img" aria-label="Subtraction app icon"></div>Beetle<br>Maths</div>

<div class="abs btn-solid view-all">VIEW ALL APP</div>

<!-- curriculum -->
<svg class="abs curriculum-bg" viewBox="0 0 1200 480" aria-hidden="true">
  <polygon points="0,23 460,23 520,462 0,462" fill="var(--orange)"/>
</svg>
<svg class="abs curriculum-bg" viewBox="0 0 1200 480" role="img" aria-label="Schoolchildren using a tablet together in class">
  <defs><linearGradient id="classPhoto" x1="0" x2="1"><stop offset="0" stop-color="#3b3f52"/><stop offset=".5" stop-color="#a07a6a"/><stop offset="1" stop-color="#2b2e3c"/></linearGradient></defs>
  <polygon points="460,23 1200,8 1200,458 520,462" fill="url(#classPhoto)"/>
</svg>
<div class="abs toy" role="img" aria-label="Plush monkey toy"></div>
<h2 class="abs curr-title">Our Curriculum</h2>
<div class="abs curr-item" style="left:77px;top:1726px"><svg width="16" height="16" viewBox="0 0 16 16"><circle cx="8" cy="8" r="7" fill="none" stroke="#fff" stroke-width="1.6"/><path d="M4.5 8.2l2.3 2.3 4.6-4.8" fill="none" stroke="#fff" stroke-width="1.8"/></svg>Australian<br>Curriculum</div>
<div class="abs curr-item" style="left:254px;top:1726px"><svg width="16" height="16" viewBox="0 0 16 16"><circle cx="8" cy="8" r="7" fill="none" stroke="#fff" stroke-width="1.6"/><path d="M4.5 8.2l2.3 2.3 4.6-4.8" fill="none" stroke="#fff" stroke-width="1.8"/></svg>Common Core<br>State Standards</div>
<div class="abs curr-item" style="left:77px;top:1816px"><svg width="16" height="16" viewBox="0 0 16 16"><circle cx="8" cy="8" r="7" fill="none" stroke="#fff" stroke-width="1.6"/><path d="M4.5 8.2l2.3 2.3 4.6-4.8" fill="none" stroke="#fff" stroke-width="1.8"/></svg>The UK School<br>Curriculum</div>
<div class="abs curr-item" style="left:254px;top:1816px"><svg width="16" height="16" viewBox="0 0 16 16"><circle cx="8" cy="8" r="7" fill="none" stroke="#fff" stroke-width="1.6"/><path d="M4.5 8.2l2.3 2.3 4.6-4.8" fill="none" stroke="#fff" stroke-width="1.8"/></svg>New Zealand<br>Curriculum</div>

<!-- testimonial -->
<svg class="abs quote-bg" viewBox="0 0 900 290" aria-hidden="true">
  <polygon points="510,255 845,262 840,288 505,275" fill="var(--blue)"/>
  <polygon points="0,12 890,0 878,262 22,250" fill="var(--grey-panel)"/>
</svg>
<div class="abs avatar" role="img" aria-label="Client portrait"></div>
<p class="abs quote">“Lorem Ipsum is simply dummy text of the printing and typesetting industry. Lorem Ipsum has been the industry’s standard dummy text ever since the 1500s, when an unknown ”</p>
<div class="abs client">CLIENT NAME</div>

<!-- feedback -->
<h2 class="abs section-title fb-title">Send Your Feedback</h2>
<p class="abs fb-sub">I really want you to make me a new app for ...</p>
<div class="abs field" style="top:2331px;height:50px">Enter Name *</div>
<div class="abs field" style="top:2394px;height:100px">Message *</div>
<div class="abs field" style="top:2509px;height:49px">Enter Email *</div>
<div class="abs btn-solid post">POST IDEA</div>

<!-- footer -->
<svg class="abs footer-bg" viewBox="0 0 1200 449" aria-hidden="true">
  <polygon points="0,120 1200,90 1200,449 0,449" fill="var(--orange)"/>
  <polygon points="0,140 180,130 0,449" fill="var(--peach)"/>
  <polygon points="1200,190 1200,449 1080,449" fill="var(--blue)"/>
</svg>
<div class="abs kids" role="img" aria-label="Group of smiling children lying on the floor"></div>
<div class="abs foot-brand"><span class="dot"></span>Quiet Pebble Apps</div>
<div class="abs social" aria-label="Social links">
  <span style="background:#2b4a8a"></span><span style="background:#c62a2a"></span><span style="background:#e26a1a"></span><span style="background:#2a9fe0"></span>
</div>
<ul class="abs foot-links"><li>Home</li><li>Apps</li><li>Curriculum</li><li>Support</li><li>Blog</li><li>Feedback</li></ul>
<p class="abs copyright">©Quiet Pebble Apps - 2018 All Right Reserved.</p>

</body>
</html>
```